Halvik - consultancy website

I need a new design for my webpage/presence [to be functioning with Wordpress - I have a programmer to set it up but not the design idea].
My company is Halvik - a consultancy firm focused on growth management for Swedish SME's primarily;. We call it Leadership toolkit for firms on the rise, kind of a doctor helping small become big. Contentwise, its a simple frontpage + 3-4 subpages with content re company/myself/focus etc. The new site should communicate a fresh, trustworthy take yet simple and functional on all devices [i.e. think UI compatible for mobile/tablet]. Current building parts/form elements are
a) existing logo and text elements
b) existing pictures
c) the yellowish color
colours and new ideas on pictures/positioning are welcome. I prefer a 'full width page' solution with centralised text elements but that's all up to you to suggest. Current site is a quickfix made by myself - now I'm moving it to a new platform so want to take the opportunity to make it
Nothing superspecial as it is a 2-man show; on the other hand I still want to have a modern & fresh reflection of my brand in digital environments. Help me out!
www.halvik-demo.se
Best
Lina Bergqvist

```html
<!DOCTYPE html>
<html lang="en">
<head>
<meta charset="utf-8">
<title>Halvik – Leadership toolkit for firms on the rise</title>
<link rel="stylesheet" href="https://fonts.googleapis.com/css2?family=Roboto:wght@300;400;500;700&display=swap">
<style>
:root{
  --orange:#f5a623;
  --green:#7cb342;
  --green-light:#8fc356;
  --green-dark:#5e9a2c;
  --pink:#e6248a;
  --pink-dark:#c81a74;
  --ink:#444;
  --muted:#777;
  --white:#fff;
  --footer:#2f2f2f;
}
*{box-sizing:border-box;margin:0;padding:0}
html,body{width:1200px;height:2832px;overflow:hidden;background:var(--white)}
body{font-family:"Roboto",Arial,sans-serif;color:var(--ink);position:relative}
.site-header{height:48px;display:flex;align-items:center;justify-content:space-between;padding:0 70px 0 70px}
.logo{font-size:40px;font-weight:700;color:#555;letter-spacing:-1px}
.nav{display:flex;gap:34px;font-size:13px;color:#666}
.nav .active{color:var(--orange)}
.hero{position:relative;height:572px;background:linear-gradient(135deg,#c9d5de 0%,#9fb0bd 45%,#6f7f8c 100%)}
.hero-caption{position:absolute;left:0;right:0;top:488px;text-align:center;font-size:44px;font-weight:300;color:var(--white);padding:0 180px;text-align:left}
.hero-caption span{background:rgba(0,0,0,.15);padding:0 10px}
.hero-dots{position:absolute;top:566px;left:0;right:0;display:flex;justify-content:center;gap:10px}
.hero-dots i{width:12px;height:12px;border-radius:50%;background:rgba(255,255,255,.6)}
.hero-dots i.on{background:var(--white)}
.welcome{height:352px;text-align:center;padding-top:64px}
.welcome h1{font-size:48px;font-weight:300;color:var(--orange)}
.welcome p{width:940px;margin:30px auto 0;font-size:14px;line-height:22px;color:var(--muted)}
.btn{display:inline-block;border:2px solid var(--orange);color:var(--orange);font-size:20px;padding:7px 20px;margin-top:40px;background:transparent}
.btn.light{border-color:var(--white);color:var(--white)}
.split{position:relative;display:flex}
.panel{padding:44px 70px 0 70px;color:var(--white)}
.panel h2{font-size:52px;font-weight:300}
.panel h3{font-size:22px;font-weight:500;margin-top:10px}
.panel p{font-size:14px;line-height:22px;margin-top:22px}
.photo{flex:1}
.what{height:516px}
.what .panel{width:620px;background:var(--green)}
.what .photo{background:linear-gradient(135deg,#dfe4e8,#aab3ba 60%,#7f8a93)}
.offer-strip{position:absolute;left:0;bottom:28px;width:620px;height:80px;display:flex;align-items:center;gap:16px;padding-left:70px;font-size:22px;font-weight:300;color:var(--white)}
.what .offer-strip{background:var(--green-light)}
.tag{background:var(--orange);color:var(--white);font-size:20px;padding:6px 14px}
.who{height:512px}
.who .photo{flex:0 0 600px;background:linear-gradient(135deg,#e8ecef,#b9c2c9 55%,#8d979f)}
.who .panel{flex:1;color:var(--ink);padding-top:48px}
.who .panel h2{color:var(--green)}
.who .panel h3{color:var(--orange);font-size:20px}
.who .panel p{color:var(--muted);font-size:13px;line-height:20px;margin-top:14px}
.why{height:568px}
.why .panel{width:660px;background:var(--pink)}
.why .photo{background:linear-gradient(135deg,#f1f1f1,#c7c7c7 55%,#a9a9a9)}
.why .offer-strip{background:var(--pink-dark);width:660px;bottom:40px}
.contact{height:152px;display:flex}
.contact > div{flex:1;padding:34px 70px;color:var(--white)}
.contact h2{font-size:40px;font-weight:300}
.get-in-touch{background:var(--green-light)}
.contact-us{background:var(--green-dark)}
.signup{display:flex;margin-top:18px;gap:8px}
.signup span{display:block;width:330px;height:36px;background:var(--white);color:#aaa;font-size:13px;padding:10px 12px}
.signup b{background:#333;font-size:14px;font-weight:400;padding:10px 16px}
.contact-line{display:flex;gap:34px;margin-top:24px;font-size:18px;align-items:center}
.contact-line span{display:flex;align-items:center;gap:8px}
.site-footer{height:112px;background:var(--footer);display:flex;justify-content:space-between;align-items:center;padding:0 70px;color:#aaa}
.site-footer .logo{color:#ddd;font-size:36px}
.site-footer small{display:block;font-size:11px;margin-top:6px}
.connect{display:flex;align-items:center;gap:10px;font-size:16px}
.connect i{width:32px;height:32px;border:2px solid #aaa;border-radius:50%}
</style>
</head>
<body>
<header class="site-header">
  <div class="logo">Halvik.</div>
  <nav class="nav"><span class="active">Home</span><span>What We Do</span><span>Who We Are</span><span>Why Us</span><span>Contact Us</span></nav>
</header>

<section class="hero" role="img" aria-label="Photo of business people shaking hands around a meeting table">
  <div class="hero-caption"><span>Leadership toolkit for firms on the rise</span></div>
  <div class="hero-dots"><i></i><i class="on"></i><i></i><i></i></div>
</section>

<section class="welcome">
  <h1>Welcome to Halvik</h1>
  <p>We help small and medium sized companies take the next step. With practical tools, clear structure and hands-on leadership support we turn ambitious plans into steady growth. Our approach is simple: understand where you stand, agree where you want to go, and build the path together with your team.</p>
  <span class="btn">Read More</span>
</section>

<section class="split what">
  <div class="panel">
    <h2>What We Do</h2>
    <h3>Progress - Just in time</h3>
    <p>Consultancy services aimed at firms with growth ambitions that need to organise, manage and fund the next stage of their development.</p>
    <p>We deliver structure, routines and leadership support when growth starts to strain the organisation – exactly when it is needed.</p>
    <p>In short: an experienced partner who knows where you want to go.</p>
    <span class="btn light">Read More</span>
  </div>
  <div class="photo" role="img" aria-label="Photo of hands fitting metal gears together"></div>
  <div class="offer-strip">Growth plans? Download Halvik's <span class="tag">Kickstart offer (SW)</span></div>
</section>

<section class="split who">
  <div class="photo" role="img" aria-label="Photo of a smiling business team in an office"></div>
  <div class="panel">
    <h2>Who We Are</h2>
    <h3>Growth enabler</h3>
    <p>Independent consulting across several industries, supporting businesses in their growth from first structure to mature organisation.</p>
    <p>With a background in marketing and economics, I have spent many years in growing companies, leading change in sales, operations and business development both in Sweden and abroad.</p>
    <p>I combine proven methods with a personal approach, always focused on results you can measure.</p>
    <span class="btn">Read More</span>
  </div>
</section>

<section class="split why">
  <div class="panel">
    <h2>Why Us</h2>
    <h3>You got your act together? Congratulations.</h3>
    <p>Growing companies often reach a point where the old ways no longer work. Processes, people and finances need a new structure to carry the business forward without losing speed or spirit.</p>
    <p>We bring the experience and tools to make that step smooth, so you can focus on customers and keep building value.</p>
    <span class="btn light">Read More</span>
  </div>
  <div class="photo" role="img" aria-label="Photo of a business team joining hands"></div>
  <div class="offer-strip">Start by downloading Halvik's <span class="tag">Kickstart offer (SW)</span></div>
</section>

<section class="contact">
  <div class="get-in-touch">
    <h2>Get in Touch</h2>
    <div class="signup"><span>Enter email address</span><b>Sign Up</b></div>
  </div>
  <div class="contact-us">
    <h2>Contact Us</h2>
    <div class="contact-line">
      <span><svg width="18" height="18" viewBox="0 0 24 24"><path fill="#fff" d="M6.6 10.8a15 15 0 0 0 6.6 6.6l2.2-2.2c.3-.3.7-.4 1-.2 1.1.4 2.3.6 3.6.6.6 0 1 .4 1 1V20c0 .6-.4 1-1 1A17 17 0 0 1 3 4c0-.6.4-1 1-1h3.5c.6 0 1 .4 1 1 0 1.3.2 2.5.6 3.6.1.3 0 .7-.2 1z"/></svg>+46 10 555 01 23</span>
      <span><svg width="18" height="14" viewBox="0 0 24 18"><rect x="1" y="1" width="22" height="16" fill="none" stroke="#fff" stroke-width="2"/><path d="M1 1l11 9 11-9" fill="none" stroke="#fff" stroke-width="2"/></svg>info@halvik-demo.se</span>
    </div>
  </div>
</section>

<footer class="site-footer">
  <div><div class="logo">Halvik.</div><small>Copyright © 2014 Halvik. All Rights Reserved.</small></div>
  <div class="connect">Connect Us <i></i><i></i><i></i><i></i></div>
</footer>
</body>
</html>
```